Velmora Freightway Solutions Business cards

Would like a very unique design catchy but professional for business cards. Please use log provided.Marlon WellsCeo and Founder TransCon Logistix Solutions1-888-913-3225mwells@tlsolutionsus.comwww.tlsolutionsus.com

```html
<!DOCTYPE html>
<html lang="en">
<head>
<meta charset="utf-8">
<title>Velmora Freightway Solutions – Business Cards</title>
<link href="https://fonts.googleapis.com/css2?family=Source+Sans+3:wght@400;600;700&display=swap" rel="stylesheet">
<style>
  :root {
    --bg: #1c1c1d;
    --card: #ffffff;
    --blue: #1873c2;
    --red: #e8202a;
    --ink: #2b2b2b;
  }
  * { margin: 0; padding: 0; box-sizing: border-box; }
  html, body { width: 1200px; height: 960px; overflow: hidden; }
  body {
    background: var(--bg);
    font-family: "Source Sans 3", Arial, sans-serif;
    position: relative;
  }
  .card {
    position: absolute;
    left: 250px;
    width: 700px;
    height: 400px;
    background: var(--card);
    overflow: hidden;
  }
  .card-front { top: 50px; }
  .card-back { top: 510px; }

  /* Front */
  .front-brand {
    position: absolute;
    top: 120px; left: 0; right: 0;
    display: flex; align-items: center; justify-content: center; gap: 18px;
  }
  .brand-square { width: 34px; height: 34px; background: var(--red); }
  .front-brand .brand-name {
    font-size: 46px; font-weight: 700; color: var(--blue); letter-spacing: 1px;
  }
  .front-web {
    position: absolute;
    top: 250px; left: 60px; right: 60px;
    display: flex; align-items: center; gap: 16px;
    color: var(--ink); font-size: 17px; font-weight: 600; letter-spacing: 3px;
  }
  .front-web .rule { flex: 1; height: 2px; background: var(--blue); }

  /* Back */
  .holder { position: absolute; top: 46px; left: 40px; }
  .holder-name { font-size: 25px; font-weight: 700; color: var(--blue); letter-spacing: 0.5px; }
  .holder-title { font-size: 18px; color: var(--red); margin-top: 2px; }
  .contact-list { list-style: none; margin-top: 14px; }
  .contact-list li {
    display: flex; align-items: center; gap: 10px;
    font-size: 17px; color: var(--ink); line-height: 26px;
  }
  .contact-list svg { width: 14px; height: 14px; flex: none; }
  .back-brand {
    position: absolute; top: 50px; right: 40px;
    display: flex; align-items: center; gap: 12px;
  }
  .back-brand .brand-square { width: 22px; height: 22px; }
  .back-brand .brand-name { font-size: 27px; font-weight: 700; color: var(--blue); }
  .divider {
    position: absolute; top: 128px; left: 232px; right: 0;
    height: 2px; background: var(--red);
  }
  .address {
    position: absolute; right: 40px; bottom: 60px;
    text-align: right; font-size: 18px; color: var(--ink); line-height: 26px;
  }
  .base-band {
    position: absolute; left: 0; right: 0; bottom: 0;
    height: 10px; background: var(--blue);
  }
</style>
</head>
<body>

<section class="card card-front">
  <div class="front-brand">
    <span class="brand-square"></span>
    <span class="brand-name">Velmora Freightway Solutions</span>
  </div>
  <div class="front-web">
    <span class="rule"></span>
    <span>www.vfwayroutes.com</span>
    <span class="rule"></span>
  </div>
</section>

<section class="card card-back">
  <div class="holder">
    <div class="holder-name">DORIAN PIKE</div>
    <div class="holder-title">CEO AND FOUNDER</div>
    <ul class="contact-list">
      <li>
        <svg viewBox="0 0 16 16"><path fill="#1873c2" d="M4 1l3 3-1.5 2a9 9 0 0 0 4.5 4.5L12 9l3 3-2 3C7 15 1 9 1 3z"/></svg>
        1-888-470-6158
      </li>
      <li>
        <svg viewBox="0 0 16 16"><rect x="1" y="3" width="14" height="10" rx="1" fill="#1873c2"/><path d="M1 4l7 5 7-5" stroke="#fff" stroke-width="1.4" fill="none"/></svg>
        dpike@vfwayroutes.com
      </li>
      <li>
        <svg viewBox="0 0 16 16"><circle cx="8" cy="8" r="6.5" fill="none" stroke="#1873c2" stroke-width="1.5"/><path d="M1.5 8h13M8 1.5c-3 3.5-3 9.5 0 13M8 1.5c3 3.5 3 9.5 0 13" stroke="#1873c2" stroke-width="1.2" fill="none"/></svg>
        www.vfwayroutes.com
      </li>
    </ul>
  </div>

  <div class="back-brand">
    <span class="brand-square"></span>
    <span class="brand-name">Velmora Freightway Solutions</span>
  </div>

  <div class="divider"></div>

  <address class="address" style="font-style: normal;">
    2417 Corvell Ridge Rd<br>
    Atlanta, GA 30342
  </address>

  <div class="base-band"></div>
</section>

</body>
</html>
```